Business Card Design

New business card design

Target Market(s)

Residential & Commercial Property Managers

Industry/Entity Type

Plumbing Services

Contact Information for Business Card

Name - Rowan Keddle, title - Director, Phone Number - 0431 286 517, email - rowan@tbk-plumbing.com.au, Company ABN - 73 215 904 386,

Font styles to use
Sans Serif

Colors
0054AA
0677BA
7BADD7
CADEEF
E8F1F8

```html
<!DOCTYPE html>
<html lang="en">
<head>
<meta charset="utf-8">
<title>TBK Plumbing Services – Business Card</title>
<link rel="stylesheet" href="https://fonts.googleapis.com/css2?family=Montserrat:wght@300;400;700&display=swap">
<style>
  :root {
    --backdrop: #222222;
    --paper: #ffffff;
    --navy: #1c2028;
    --aqua: #29a8e0;
    --ink: #1c2028;
    --muted: #8a7f78;
    --light-text: #e8f1f8;
  }
  * { box-sizing: border-box; margin: 0; padding: 0; }
  html, body { width: 1200px; height: 780px; overflow: hidden; }
  body {
    background: var(--backdrop);
    font-family: "Montserrat", sans-serif;
    position: relative;
  }
  .card {
    position: absolute;
    top: 244px;
    width: 510px;
    height: 292px;
    background: var(--paper);
    overflow: hidden;
    box-shadow: 0 14px 30px rgba(0,0,0,.45);
  }
  .card--contact { left: 50px; }
  .card--brand { left: 640px; }

  .card__wave { position: absolute; inset: 0; width: 100%; height: 100%; }

  .wordmark { position: absolute; color: var(--ink); }
  .wordmark__name {
    font-weight: 300;
    letter-spacing: 6px;
    line-height: 1;
    display: flex;
    align-items: center;
  }
  .wordmark__dot {
    display: inline-block;
    border-radius: 50%;
    background: var(--aqua);
  }
  .wordmark__tagline {
    color: var(--muted);
    font-weight: 400;
    text-transform: lowercase;
  }

  .card--contact .wordmark { left: 46px; top: 20px; }
  .card--contact .wordmark__name { font-size: 62px; }
  .card--contact .wordmark__dot { width: 15px; height: 15px; margin-left: 10px; }
  .card--contact .wordmark__tagline { font-size: 9px; letter-spacing: 8px; margin-top: 5px; padding-left: 4px; }

  .card--brand .wordmark { left: 0; right: 0; top: 82px; text-align: center; }
  .card--brand .wordmark__name { font-size: 96px; justify-content: center; }
  .card--brand .wordmark__dot { width: 20px; height: 20px; margin-left: 14px; }
  .card--brand .wordmark__tagline { font-size: 12px; letter-spacing: 12px; margin-top: 10px; }

  .abn {
    position: absolute;
    left: 20px; top: 226px;
    color: var(--light-text);
    font-size: 11px; font-weight: 300; line-height: 1.4;
  }
  .person {
    position: absolute;
    right: 40px; top: 150px;
    text-align: right;
  }
  .person__name { color: var(--aqua); font-size: 22px; font-weight: 700; line-height: 1.1; }
  .person__title { color: var(--light-text); font-size: 13px; font-weight: 300; }
  .accent-block {
    position: absolute;
    right: 0; top: 168px;
    width: 26px; height: 34px;
    background: var(--aqua);
  }
  .contact-list {
    position: absolute;
    right: 18px; top: 216px;
    list-style: none;
    text-align: right;
    color: var(--light-text);
    font-size: 13px; font-weight: 300;
  }
  .contact-list li { display: flex; align-items: center; justify-content: flex-end; gap: 8px; margin-bottom: 10px; }
  .contact-list svg { width: 14px; height: 14px; fill: var(--aqua); }
</style>
</head>
<body>

  <section class="card card--contact" aria-label="Business card, contact side">
    <svg class="card__wave" viewBox="0 0 510 292" preserveAspectRatio="none" aria-hidden="true">
      <path fill="var(--aqua)" d="M0,172 C80,198 160,134 260,114 C360,96 440,82 510,20 L510,292 L0,292 Z"/>
      <path fill="var(--paper)" d="M0,182 C80,207 160,143 260,123 C360,105 440,92 510,32 L510,292 L0,292 Z"/>
      <path fill="var(--navy)" d="M0,190 C80,214 160,150 260,130 C360,112 440,100 510,42 L510,292 L0,292 Z"/>
    </svg>

    <div class="wordmark">
      <div class="wordmark__name">tbk<span class="wordmark__dot"></span></div>
      <div class="wordmark__tagline">plumbing services</div>
    </div>

    <p class="abn">Company ABN<br>- 73 215 904 386</p>

    <div class="person">
      <p class="person__name">Rowan Keddle</p>
      <p class="person__title">Director</p>
    </div>
    <span class="accent-block" aria-hidden="true"></span>

    <ul class="contact-list">
      <li>0431 286 517
        <svg viewBox="0 0 24 24" aria-hidden="true"><path d="M6.6 10.8a15.1 15.1 0 0 0 6.6 6.6l2.2-2.2a1 1 0 0 1 1-.25 11.4 11.4 0 0 0 3.6.57 1 1 0 0 1 1 1V20a1 1 0 0 1-1 1A17 17 0 0 1 3 4a1 1 0 0 1 1-1h3.5a1 1 0 0 1 1 1c0 1.25.2 2.450.57 3.57a1 1 0 0 1-.25 1z"/></svg>
      </li>
      <li>rowan@tbk-plumbing.com.au
        <svg viewBox="0 0 24 24" aria-hidden="true"><path d="M3 5h18a1 1 0 0 1 1 1v12a1 1 0 0 1-1 1H3a1 1 0 0 1-1-1V6a1 1 0 0 1 1-1zm9 7.2L4.2 7H19.8zM4 9v8h16V9l-8 5.3z"/></svg>
      </li>
    </ul>
  </section>

  <section class="card card--brand" aria-label="Business card, brand side">
    <div class="wordmark">
      <div class="wordmark__name">tbk<span class="wordmark__dot"></span></div>
      <div class="wordmark__tagline">plumbing services</div>
    </div>
  </section>

</body>
</html>
```